Hardcore nerd needs to stand out in a sea of dull Defence business cards

Wombarra Devices is a new Australian consulting engineering company that turns research and theory into practical systems. No evangelistic fluff, just mathematics and physics into electronic and optical circuits for consumer products, scientific research or Defence applications.

We already have a recognised logo (provided) which is often dark blue/black on a light background but we're open to other combinations. (Us engineers tend to have limited aesthetic imagination :)

Some of our recent products have included:
* Instrumentation for electrical testing,
* Radar jammers,
* GPS antenna design,
* Satellite tracking systems,
* High power lasers

We're open to both single and double-sided designs - happy to be convinced either way.

P.S. Another group is working on the web page, so - alas - our web site is currently of no use for images/ideas...

Target Market(s)

Engineering managers,
Scientists

Contact Information for Business Card

Dr Colin Harte
R&D Engineer

colin@wombarradevices.com.au
0427 563 710

PO Box XXX (to be confirmed)
Kelsby ACT 2917
Australia

Font styles to use
Serif
Sans Serif

Colors

Designer to choose colors to be used in the design.

Requirements
Must have
• My contact details!
• I've had many (great) "bold and plain" designs submitted already, so feel free to be artistically creative :)
• Happy to take advice re fonts/colours/printability etc.
Nice to have
• I'm not sure if "lists" are more at home on a CV than a business card, but representative services include:
• Applied electromagnetics
• RF and high speed electronics
• Signal and image processing
• Electro-optical and laser systems
• Concept-to-prototype design services
• If you're considering double sided cards, then often measuring/alignment grids/rulers feature on the back of similar cards.
• e.g. https://www.veltranoptics.example/newgrouppage9.cfm?objectgroup_id=4183
• https://www.veltranoptics.example/newgrouppage9.cfm?objectgroup_ID=4185
• ..or even a "Smith chart" (google will return lots)
• Generic images to represent a capability might work - googling images associated with keyword for each of these areas might help:
• - "passive radar", "phased array", "fdtd", "vircator"
• RF and high speed electronic design
• - "smith chart", "microstrip circuits", "dimensioned drawing", "electronic schematic"
• - "dft", "iir filter"
• - "optical cavity". "laser energy level diagram"
• Background/watermarked images outlines/wireframes/schematics would probably look OK.
Should not have
• If a list of projects/services is provided, it is important not to make the client feel that this is "all" the company can do. Engineering design is a creative discipline (like graphics :)
• Please, no stock "military" snaps like planes, missiles, etc!

```html
<!DOCTYPE html>
<html lang="en">
<head>
<meta charset="utf-8">
<title>Wombarra Devices – Business Card</title>
<link href="https://fonts.googleapis.com/css2?family=Lato:wght@400;700;900&display=swap" rel="stylesheet">
<style>
  :root {
    --navy: #1f2a66;
    --orange: #f47e20;
    --white: #ffffff;
    --ink: #2b2b2b;
    --backdrop: #e8e5e0;
    --card-w: 340px;
    --card-h: 560px;
    --radius: 22px;
  }
  * { margin: 0; padding: 0; box-sizing: border-box; }
  html, body {
    width: 1200px; height: 902px; overflow: hidden;
    background: var(--backdrop);
    font-family: "Lato", sans-serif;
  }
  .stage {
    width: 1200px; height: 902px;
    display: flex; justify-content: center; align-items: center; gap: 120px;
  }
  .card {
    position: relative;
    width: var(--card-w); height: var(--card-h);
    border-radius: var(--radius);
    overflow: hidden;
    box-shadow: 0 6px 18px rgba(0,0,0,0.18);
  }

  /* Brand lockup */
  .brand { display: flex; align-items: center; gap: 12px; }
  .brand-dot { width: 34px; height: 34px; border-radius: 50%; flex: none; }
  .brand-name {
    font-weight: 900; font-size: 23px; line-height: 1.05;
    letter-spacing: 1px; text-transform: uppercase;
  }

  /* Front */
  .card-front { background: var(--white); }
  .card-front .brand { position: absolute; top: 62px; left: 0; right: 0; justify-content: center; }
  .card-front .brand-dot { background: var(--navy); }
  .card-front .brand-name { color: var(--navy); }
  .person { position: absolute; top: 170px; left: 0; right: 0; text-align: center; }
  .person-name { color: var(--navy); font-weight: 700; font-size: 22px; }
  .person-role { color: var(--orange); font-size: 15px; margin-top: 2px; }
  .contact { position: absolute; top: 250px; left: 30px; color: var(--ink); font-size: 15.5px; line-height: 1.45; }
  .contact-icons { display: flex; gap: 8px; padding-bottom: 5px; margin-bottom: 6px; border-bottom: 1.5px solid var(--navy); width: 40px; }
  .capabilities {
    position: absolute; left: 0; right: 0; bottom: 0; height: 210px;
    background: var(--orange); color: var(--white);
    padding: 26px 26px 0 20px; text-align: right;
    font-size: 17.5px; line-height: 1.25; list-style: none;
  }

  /* Back */
  .card-back { background: var(--orange); }
  .card-back .brand { position: absolute; top: 200px; left: 0; right: 0; justify-content: center; }
  .card-back .brand-dot { background: var(--white); }
  .card-back .brand-name { color: var(--navy); }
  .address { position: absolute; left: 30px; bottom: 34px; color: var(--white); font-size: 15.5px; line-height: 1.35; }
</style>
</head>
<body>
<main class="stage">
  <section class="card card-front">
    <div class="brand">
      <span class="brand-dot"></span>
      <span class="brand-name">Wombarra<br>Devices</span>
    </div>
    <div class="person">
      <p class="person-name">Dr Colin Harte</p>
      <p class="person-role">R&amp;D Engineer</p>
    </div>
    <div class="contact">
      <div class="contact-icons">
        <svg width="13" height="13" viewBox="0 0 24 24" aria-label="phone"><path fill="#f47e20" d="M6.6 10.8a15 15 0 0 0 6.6 6.6l2.2-2.2a1 1 0 0 1 1-.25 11.4 11.4 0 0 0 3.6.57 1 1 0 0 1 1 1V20a1 1 0 0 1-1 1A17 17 0 0 1 3 4a1 1 0 0 1 1-1h3.5a1 1 0 0 1 1 1c0 1.25.2 2.45.57 3.57a1 1 0 0 1-.25 1z"/></svg>
        <svg width="14" height="13" viewBox="0 0 24 22" aria-label="email"><rect x="2" y="4" width="20" height="15" rx="2" fill="none" stroke="#f47e20" stroke-width="2.4"/><path d="M3 5l9 7 9-7" fill="none" stroke="#f47e20" stroke-width="2.4"/></svg>
      </div>
      <p>0427 563 710</p>
      <p>colin@wombarradevices.com.au</p>
    </div>
    <ul class="capabilities">
      <li>Radar jammers,</li>
      <li>High power lasers,</li>
      <li>GPS antenna design,</li>
      <li>Satellite tracking systems,</li>
      <li>Instrumentation for electrical testing</li>
    </ul>
  </section>

  <section class="card card-back">
    <div class="brand">
      <span class="brand-dot"></span>
      <span class="brand-name">Wombarra<br>Devices</span>
    </div>
    <div class="address">
      <p>PO Box XXX</p>
      <p>Kelsby ACT 2917, Australia</p>
    </div>
  </section>
</main>
</body>
</html>
```